Alaska Law Firm Needs a Sticker Design

We need a design for stickers to put on already-printed brochures. We mail the brochures to potential clients so they can learn more about accident-induced injuries, insurance claims, legal representation, and our own law firm.

One of our lawyers wrote a book that provides a helpful overview of personal injury claims. We are offering this book for free to anyone who calls and requests it. Therefore, the sticker design should include one of the following phrases, or something very similar:
a) "Still have questions? Call and request our book-- for free!"
b) "Still have questions about auto accident claims? Call and request our book today."
c) "Still have questions about filing a claim? Call and request a free copy of our book."
d) "Still have questions? Call us today to request a free copy of our book, Clear Lanes Ahead."
e) "To learn more about automobile accidents and insurance, call today and request a free copy of our book."

The sticker should be approximately 3"x3" and may be a circle, square, rectangle, or ellipsis. The sticker will be placed on the back of the folder, which is light blue. We would like the sticker to match the color scheme of our website and the folder.

I will upload an image of the book cover as soon as I obtain it.

Law Firm

Font styles to use
Serif
Sans Serif

Requirements
Should not have
• Bright colors that aren't already used in the folder design. e.g. no bright orange, pink, chartreuse, turquoise, yellow, red.

```html
<!DOCTYPE html>
<html lang="en">
<head>
<meta charset="utf-8">
<title>Free Book Sticker</title>
<link href="https://fonts.googleapis.com/css2?family=Bebas+Neue&family=Open+Sans:wght@400;800&family=Montserrat:wght@500&display=swap" rel="stylesheet">
<style>
  :root {
    --navy: #143f69;
    --white: #ffffff;
    --backdrop: #e9e9e9;
    --cover-navy: #1b2a5c;
    --photo-sky: #cfe3ef;
    --photo-grass: #7fae4a;
    --book-edge: #b9b9b9;
  }
  html, body { margin: 0; padding: 0; overflow: hidden; }
  body { width: 1200px; height: 855px; background: var(--backdrop); position: relative; font-family: "Bebas Neue", sans-serif; }
  .sticker { position: absolute; left: 0; top: 0; width: 1200px; height: 855px; }
  .sticker-shape { position: absolute; left: 0; top: 0; }
  .headline, .subhead, .cta, .phone, .free { position: absolute; margin: 0; text-align: center; color: var(--white); line-height: 1; white-space: nowrap; }
  .headline { left: 300px; width: 600px; top: 165px; font-size: 130px; }
  .subhead { left: 300px; width: 600px; top: 281px; font-size: 85px; letter-spacing: 0.14em; padding-left: 0.14em; box-sizing: border-box; }
  .cta { left: 280px; width: 430px; top: 435px; font-size: 50px; letter-spacing: -0.01em; color: var(--navy); }
  .phone { left: 280px; width: 430px; top: 490px; font-family: "Montserrat", sans-serif; font-weight: 500; font-size: 50px; color: var(--navy); }
  .free { left: 400px; width: 400px; top: 590px; font-size: 161px; }
  .book { position: absolute; left: 702px; top: 360px; width: 164px; height: 266px; background: var(--white); box-shadow: 6px 6px 0 var(--book-edge); font-family: "Open Sans", sans-serif; overflow: hidden; }
  .book-author { margin: 14px 0 0; text-align: center; font-size: 10px; color: #555; }
  .book-title { margin: 4px 0 0; text-align: center; font-weight: 800; font-size: 19px; line-height: 1; color: var(--cover-navy); }
  .book-photo { position: absolute; left: 8px; top: 78px; width: 148px; height: 146px; background: linear-gradient(180deg, var(--photo-sky) 0%, #a9cf83 55%, var(--photo-grass) 100%); }
  .book-tagline { position: absolute; left: 0; bottom: 0; width: 100%; height: 42px; background: var(--cover-navy); color: var(--white); font-size: 8px; text-align: center; display: flex; align-items: center; justify-content: center; text-transform: uppercase; line-height: 1.3; }
</style>
</head>
<body>
  <div class="sticker">
    <svg class="sticker-shape" width="1200" height="855" viewBox="0 0 1200 855" aria-hidden="true">
      <defs><clipPath id="disc"><circle cx="600" cy="428" r="340"/></clipPath></defs>
      <circle cx="600" cy="428" r="357" fill="var(--white)"/>
      <circle cx="600" cy="428" r="340" fill="var(--navy)"/>
      <rect x="240" y="402" width="720" height="172" fill="var(--white)" clip-path="url(#disc)"/>
    </svg>
    <p class="headline">Still Have</p>
    <p class="subhead">Questions?</p>
    <p class="cta">Call &amp; Request Our Book</p>
    <p class="phone">(907) 555-0148</p>
    <p class="free">Free</p>
    <div class="book">
      <p class="book-author">DANIEL R. HOLLIS</p>
      <p class="book-title">CLEAR LANES<br>AHEAD</p>
      <div class="book-photo" role="img" aria-label="Cover photo of a smiling family lying on grass in a park beside a red car"></div>
      <div class="book-tagline">The right way to handle<br>your auto accident claim</div>
    </div>
  </div>
</body>
</html>
```